Change of trading name, rebrand

existing website to be updated with new theme and logo. existing website is
www.harlowbrentmere.com.au
Industry/Entity Type
Construction
Coding
Coded - Design and coding required
Number of Pages Required
5+ page
Requirements
Must have
- be mobile phone friendly

```html
<!DOCTYPE html>
<html lang="en">
<head>
<meta charset="utf-8">
<title>Harlow Brentmere Resources – Plant Hire</title>
<link href="https://fonts.googleapis.com/css2?family=Russo+One&family=Roboto:wght@400;500;700&display=swap" rel="stylesheet">
<style>
:root{
  --navy:#252a7f;
  --navy-deep:#1c2070;
  --ink:#111;
  --text:#222;
  --muted:#666;
  --panel:#f4f4f4;
  --white:#fff;
  --black:#000;
}
*{box-sizing:border-box;margin:0;padding:0}
html,body{width:1200px;height:4518px;overflow:hidden}
body{position:relative;font-family:"Roboto",Arial,sans-serif;color:var(--text);background:var(--white)}
.abs{position:absolute}
.head{font-family:"Russo One","Arial Black",sans-serif;color:var(--ink);text-transform:uppercase;letter-spacing:.5px}
.btn{position:absolute;display:flex;align-items:center;justify-content:center;gap:7px;font-weight:700;font-size:13px;text-transform:uppercase;color:var(--white);background:var(--navy);clip-path:polygon(12px 0,100% 0,calc(100% - 12px) 100%,0 100%)}
.btn.outline{background:none;color:var(--navy);clip-path:none}
.btn.outline svg.frame{position:absolute;inset:0}
.btn .dot{width:11px;height:11px;border-radius:50%;background:currentColor;display:inline-block;position:relative}
.btn .dot::after{content:"";position:absolute;left:3px;top:3px;border-left:5px solid var(--navy);border-top:2.5px solid transparent;border-bottom:2.5px solid transparent}
.btn.outline .dot::after{border-left-color:var(--white)}
.btn.dark .dot::after{border-left-color:var(--black)}
.btn.dark{background:var(--black)}
.photo{position:absolute}
.emblem{position:absolute;width:80px;height:16px;left:560px}
/* header */
.topline{left:0;top:0;width:1200px;height:3px;background:var(--navy)}
.logo{left:145px;top:30px;width:140px;text-align:center}
.logo .name{font-family:"Russo One",sans-serif;font-size:42px;line-height:42px;color:var(--ink)}
.logo .sub{font-family:"Russo One",sans-serif;font-size:12px;letter-spacing:3px;color:var(--ink)}
.contact-item{display:flex;align-items:center;gap:10px}
.ic{width:36px;height:36px;border-radius:50%;background:var(--navy);display:flex;align-items:center;justify-content:center}
.contact-item small{display:block;font-size:11px;color:#444}
.contact-item b{font-size:14px;font-weight:500;color:var(--ink)}
.nav{left:365px;top:75px;width:835px;height:41px;background:var(--black);clip-path:polygon(22px 0,100% 0,100% 100%,0 100%)}
.nav a{position:absolute;top:0;height:41px;line-height:41px;color:var(--white);font-size:12.5px;font-weight:700;text-decoration:none;text-transform:uppercase}
.nav a.active{background:var(--navy);padding:0 10px}
/* hero */
.hero{left:0;top:116px;width:1200px;height:646px;background:linear-gradient(110deg,#3b3f45 0%,#5e6770 35%,#8aa0b8 60%,#b07a52 80%,#6b5a4a 100%)}
.hero-title{left:145px;top:270px;font-size:42px;line-height:48px;color:var(--white)}
.hero-sub{left:145px;top:390px;width:450px;font-size:14px;line-height:28px;color:var(--white);font-weight:500}
/* about */
.about-label{left:629px;top:800px;font-family:"Russo One",sans-serif;color:var(--navy);font-size:15px}
.about-title{left:629px;top:835px;font-size:32px;line-height:42px}
.about-text{left:629px;top:940px;width:427px;font-size:12px;line-height:24px;color:#666;text-align:justify}
.about-text p{margin-bottom:8px}
/* plant hire */
.plant{left:0;top:1296px;width:1200px;height:684px;background:var(--panel)}
.sec-title{width:1200px;left:0;text-align:center;font-size:32px}
.card{position:absolute;width:288px;height:410px;background:var(--white);border-radius:8px;box-shadow:0 3px 12px rgba(0,0,0,.15);text-align:center}
.card .img{position:absolute;left:8px;top:8px;width:272px;height:200px}
.card h3{position:absolute;top:232px;width:100%;font-size:16px;font-weight:500;color:var(--ink)}
.card p{position:absolute;top:262px;left:30px;width:228px;font-size:12px;line-height:21px;color:#666}
.arrow{position:absolute;width:24px;height:40px}
/* why */
.why{left:0;top:1980px;width:600px;height:468px;background:var(--navy)}
.why-item{position:absolute;display:flex;align-items:center;gap:14px;color:var(--white);font-size:14.5px;font-weight:700;line-height:24px}
.why-item svg{width:50px;height:50px;flex:none;fill:none;stroke:var(--white);stroke-width:2;stroke-linecap:round;stroke-linejoin:round}
/* projects */
.proj{position:absolute}
.proj-cap{position:absolute;inset:0;display:flex;align-items:center;justify-content:center;color:var(--white);font-size:15px;font-weight:700;background:rgba(37,42,127,.75)}
/* clients */
.clients{left:0;top:3213px;width:1200px;height:320px;background:var(--panel)}
.client{position:absolute;top:3375px;height:78px;background:var(--white);border-radius:4px;display:flex;align-items:center;justify-content:center;gap:8px;font-size:20px;font-weight:700;color:var(--navy)}
.client i{width:14px;height:14px;background:var(--navy);display:block}
.circ-arrow{position:absolute;width:28px;height:28px;border-radius:50%;background:var(--white);box-shadow:0 1px 4px rgba(0,0,0,.2);display:flex;align-items:center;justify-content:center}
/* contact */
.contact{left:0;top:3500px;width:1200px;height:710px;background:var(--navy)}
.field{position:absolute;background:var(--white);font-size:12px;color:#777;padding:18px 20px}
/* footer */
.footer{left:0;top:4210px;width:1200px;height:308px;background:var(--black);color:var(--white)}
.flinks{position:absolute;top:4292px;left:357px;display:flex;gap:22px;font-size:13.5px;color:var(--white)}
.social{position:absolute;top:4285px;width:30px;height:30px;border-radius:50%;background:#2a2a2a;border:1px solid #555}
.finfo{position:absolute;top:4370px;display:flex;gap:12px;color:var(--white)}
.finfo .fic{width:26px;height:26px;border-radius:50%;background:var(--navy);flex:none;display:flex;align-items:center;justify-content:center}
.finfo b{display:block;font-size:13px;font-weight:700}
.finfo span{font-size:12px}
.copy{position:absolute;top:4462px;left:0;width:1200px;text-align:center;font-size:13px;color:var(--white)}
</style>
</head>
<body>

<!-- Header -->
<div class="abs topline"></div>
<div class="abs logo"><div class="name">HBR</div><div class="sub">PLANT HIRE</div></div>

<div class="abs contact-item" style="left:457px;top:22px">
  <div class="ic"><svg width="16" height="12" viewBox="0 0 16 12"><rect x="0.5" y="0.5" width="15" height="11" fill="none" stroke="#fff"/><path d="M1 1l7 6 7-6" fill="none" stroke="#fff"/></svg></div>
  <div><small>Email Us On</small><b>info@harlowbrentmere.com</b></div>
</div>
<div class="abs contact-item" style="left:707px;top:22px">
  <div class="ic"><svg width="16" height="16" viewBox="0 0 24 24"><path d="M6.6 10.8c1.4 2.8 3.8 5.1 6.6 6.6l2.2-2.2c.3-.3.7-.4 1-.2 1.1.4 2.3.6 3.6.6.6 0 1 .4 1 1V20c0 .6-.4 1-1 1C10.6 21 3 13.4 3 4c0-.6.4-1 1-1h3.5c.6 0 1 .4 1 1 0 1.3.2 2.5.6 3.6.1.3 0 .7-.2 1z" fill="#fff"/></svg></div>
  <div><small>Call Us Today</small><b style="font-size:17px">1300 462 915</b></div>
</div>
<div class="btn" style="left:903px;top:20px;width:152px;height:38px">FREE QUOTE</div>

<nav class="abs nav">
  <a class="active" style="left:45px">Home</a>
  <a style="left:118px">About Us</a>
  <a style="left:209px">Plant Hire ▾</a>
  <a style="left:327px">Major Project</a>
  <a style="left:463px">Policies</a>
  <a style="left:548px">Jobs</a>
  <a style="left:608px">Contact Us</a>
</nav>

<!-- Hero -->
<div class="abs hero" role="img" aria-label="Orange excavator working on a dusty construction site"></div>
<h1 class="abs head hero-title">Harlow Brentmere<br>Resources</h1>
<p class="abs hero-sub">Harlow Brentmere Heavy Equipment Hire specialise in the hire of heavy earthmoving, mining and construction</p>
<div class="btn" style="left:145px;top:470px;width:172px;height:46px">Get Started</div>
<svg class="abs" style="left:570px;top:628px" width="60" height="14" viewBox="0 0 60 14">
  <circle cx="7" cy="7" r="5" fill="#fff"/><circle cx="21" cy="7" r="4.5" fill="none" stroke="#fff"/><circle cx="35" cy="7" r="4.5" fill="none" stroke="#fff"/><circle cx="49" cy="7" r="4.5" fill="none" stroke="#fff"/>
</svg>
<svg class="abs" style="left:0;top:600px" width="1200" height="165" viewBox="0 0 1200 165">
  <polygon points="420,120 1200,15 1200,165 0,165" fill="var(--navy)"/>
  <polygon points="0,162 1200,100 1200,165 0,165" fill="#fff"/>
</svg>

<!-- About -->
<div class="abs" role="img" aria-label="Excavator being lifted by crane onto a barge" style="left:145px;top:810px;width:364px;height:364px;border-radius:50%;background:linear-gradient(160deg,#9fb7d6,#c0a08a 70%,#7a6a5a)"></div>
<div class="abs" role="img" aria-label="Company owner standing beside machinery" style="left:380px;top:1034px;width:160px;height:160px;border-radius:50%;border:5px solid #fff;background:linear-gradient(160deg,#c9d7e6,#5b7cb3 60%,#d07a3c)"></div>
<div class="abs about-label">ABOUT US</div>
<svg class="abs" style="left:728px;top:802px" width="56" height="14" viewBox="0 0 56 14"><line x1="0" y1="7" x2="20" y2="7" stroke="var(--navy)" stroke-width="2"/><rect x="24" y="3" width="8" height="8" fill="var(--navy)" transform="rotate(45 28 7)"/><line x1="36" y1="7" x2="56" y2="7" stroke="var(--navy)" stroke-width="2"/></svg>
<h2 class="abs head about-title">HBR Heavy Equipment<br>Hire Services.</h2>
<div class="abs about-text">
  <p>Harlow Brentmere Heavy Equipment Hire specialise in the hire of heavy earthmoving, mining and construction machines with specialised attachments and tooling. Our array of machines and attachments is second to none, and we have one of the largest hire fleets available in South East Queensland.</p>
  <p>If its plant hire you require, then Harlow Brentmere Resources, or HBR as the local's call us – should be the first call you make.</p>
</div>
<div class="btn" style="left:629px;top:1154px;width:181px;height:46px">Learn More <span class="dot" style="background:#fff"></span></div>

<!-- Plant Hire -->
<div class="abs plant"></div>
<svg class="emblem" style="top:1352px" viewBox="0 0 80 16"><line x1="4" y1="8" x2="30" y2="8" stroke="var(--navy)" stroke-width="2"/><rect x="35" y="3" width="10" height="10" fill="var(--navy)" transform="rotate(45 40 8)"/><line x1="50" y1="8" x2="76" y2="8" stroke="var(--navy)" stroke-width="2"/></svg>
<h2 class="abs head sec-title" style="top:1380px">Plant Hire</h2>

<svg class="arrow" style="left:60px;top:1640px" viewBox="0 0 24 40"><path d="M18 6L6 20l12 14" fill="none" stroke="#111" stroke-width="4"/></svg>
<svg class="arrow" style="left:1114px;top:1640px" viewBox="0 0 24 40"><path d="M6 6l12 14L6 34" fill="none" stroke="#111" stroke-width="4"/></svg>

<div class="card" style="left:145px;top:1455px">
  <div class="img" role="img" aria-label="Wheeled excavator on site" style="background:linear-gradient(170deg,#9fb2c7,#6f5648 60%,#3c3835)"></div>
  <h3>Excavators &amp; Diggers For Hire</h3>
  <p>We are proud of our broad range of excavators fitted with state-of-the-art GPS, spanning reliable</p>
  <div class="btn outline" style="left:63px;top:345px;width:162px;height:38px"><svg class="frame" width="162" height="38"><polygon points="12,1 161,1 150,37 1,37" fill="none" stroke="var(--navy)" stroke-width="2"/></svg>Read More <span class="dot"></span></div>
</div>
<div class="card" style="left:457px;top:1470px;box-shadow:0 6px 18px rgba(0,0,0,.25)">
  <div class="img" role="img" aria-label="Yellow dozer on gravel" style="background:linear-gradient(170deg,#8fb0d8,#c8b56a 55%,#8a8576)"></div>
  <h3>Dozers For Hire</h3>
  <p>The most prolific brands of dozer manufacturers are Garrand &amp; Tesshin – and we have both machine</p>
  <div class="btn" style="left:63px;top:345px;width:162px;height:38px">Read More <span class="dot" style="background:#fff"></span></div>
</div>
<div class="card" style="left:768px;top:1455px">
  <div class="img" role="img" aria-label="Swamp dozer on sandy ground" style="background:linear-gradient(170deg,#9ec0dc,#d6c25a 55%,#9c9080)"></div>
  <h3>Swamp Dozers For Hire</h3>
  <p>The most prolific brands of dozer manufacturers are Garrand &amp; Tesshin – and we have both machine</p>
  <div class="btn outline" style="left:63px;top:345px;width:162px;height:38px"><svg class="frame" width="162" height="38"><polygon points="12,1 161,1 150,37 1,37" fill="none" stroke="var(--navy)" stroke-width="2"/></svg>Read More <span class="dot"></span></div>
</div>

<!-- Why choose us -->
<div class="abs why"></div>
<div class="photo" role="img" aria-label="Excavator digging a trench beside trucks under a cloudy sky" style="left:600px;top:1980px;width:600px;height:468px;background:linear-gradient(180deg,#a9bdd6 0%,#c6d0dc 35%,#6d6458 60%,#4b3f33 100%)"></div>
<svg class="abs" style="left:143px;top:2058px" width="80" height="16" viewBox="0 0 80 16"><line x1="0" y1="8" x2="30" y2="8" stroke="#fff" stroke-width="2"/><rect x="35" y="3" width="10" height="10" fill="#fff" transform="rotate(45 40 8)"/><line x1="50" y1="8" x2="80" y2="8" stroke="#fff" stroke-width="2"/></svg>
<h2 class="abs head" style="left:143px;top:2088px;font-size:32px;color:#fff">Why Choose Us?</h2>

<div class="why-item" style="left:143px;top:2170px">
  <svg viewBox="0 0 50 50"><circle cx="25" cy="25" r="18"/><path d="M25 14v11l8 5"/></svg>
  <span>20+ Years Of<br>Experience</span></div>
<div class="why-item" style="left:390px;top:2170px">
  <svg viewBox="0 0 50 50"><circle cx="25" cy="25" r="7"/><path d="M25 8v6M25 36v6M8 25h6M36 25h6M13 13l4 4M33 33l4 4M13 37l4-4M33 17l4-4"/><circle cx="25" cy="25" r="13"/></svg>
  <span>100+ Machines<br>In Fleet</span></div>
<div class="why-item" style="left:143px;top:2252px">
  <svg viewBox="0 0 50 50"><rect x="10" y="10" width="30" height="32"/><path d="M16 17h5M29 17h5M16 25h5M29 25h5M21 42v-9h8v9"/></svg>
  <span>One Of Qld's Largest<br>Suppliers</span></div>
<div class="why-item" style="left:390px;top:2252px">
  <svg viewBox="0 0 50 50"><path d="M34 8a9 9 0 00-9 12L10 35a4 4 0 006 6l15-15a9 9 0 0012-9l-6 6-5-1-1-5 6-6a9 9 0 00-3-3z"/></svg>
  <span>Onsite<br>Servicing</span></div>
<div class="why-item" style="left:143px;top:2332px">
  <svg viewBox="0 0 50 50"><rect x="6" y="13" width="38" height="26" rx="3"/><circle cx="19" cy="26" r="6"/><circle cx="33" cy="26" r="4"/><path d="M6 19h4M6 33h4"/></svg>
  <span>Custom Machine<br>Attachments</span></div>

<!-- Major projects -->
<svg class="emblem" style="top:2522px" viewBox="0 0 80 16"><line x1="4" y1="8" x2="30" y2="8" stroke="var(--navy)" stroke-width="2"/><rect x="35" y="3" width="10" height="10" fill="var(--navy)" transform="rotate(45 40 8)"/><line x1="50" y1="8" x2="76" y2="8" stroke="var(--navy)" stroke-width="2"/></svg>
<h2 class="abs head sec-title" style="top:2550px">Major Projects</h2>
<div class="proj" role="img" aria-label="Dozer pushing earth" style="left:153px;top:2625px;width:437px;height:198px;background:linear-gradient(170deg,#b7c4cf,#a77a52 50%,#7a5a3e)"></div>
<div class="proj" role="img" aria-label="Long reach excavator on a barge" style="left:610px;top:2625px;width:436px;height:198px;background:linear-gradient(180deg,#8fb2d8,#6b84a6 55%,#6a5b52)"></div>
<div class="proj" role="img" aria-label="Excavator on a rocky slope" style="left:153px;top:2840px;width:286px;height:196px;background:linear-gradient(170deg,#c9c4b8,#b08060 55%,#938a7e)"></div>
<div class="proj" role="img" aria-label="Excavator at rail project" style="left:457px;top:2840px;width:286px;height:196px;background:linear-gradient(170deg,#b8b2a4,#8a7a60)"><div class="proj-cap">Wulkaraka, Regional Rail</div></div>
<div class="proj" role="img" aria-label="Excavator with hammer in a tunnel" style="left:760px;top:2840px;width:286px;height:196px;background:linear-gradient(100deg,#2c2a28,#5e5650 60%,#d8d4cc)"></div>
<div class="btn" style="left:510px;top:3086px;width:181px;height:46px">Learn More <span class="dot" style="background:#fff"></span></div>

<!-- Clients -->
<div class="abs clients"></div>
<svg class="emblem" style="top:3270px" viewBox="0 0 80 16"><line x1="4" y1="8" x2="30" y2="8" stroke="var(--navy)" stroke-width="2"/><rect x="35" y="3" width="10" height="10" fill="var(--navy)" transform="rotate(45 40 8)"/><line x1="50" y1="8" x2="76" y2="8" stroke="var(--navy)" stroke-width="2"/></svg>
<h2 class="abs head sec-title" style="top:3298px">Our Clients</h2>
<div class="circ-arrow" style="left:81px;top:3401px"><svg width="10" height="10" viewBox="0 0 10 10"><polygon points="8,1 2,5 8,9" fill="#111"/></svg></div>
<div class="circ-arrow" style="left:1090px;top:3401px"><svg width="10" height="10" viewBox="0 0 10 10"><polygon points="2,1 8,5 2,9" fill="#111"/></svg></div>
<div class="client" style="left:152px;width:153px;font-size:17px"><i></i>Carrow Civil</div>
<div class="client" style="left:337px;width:153px">Pellard</div>
<div class="client" style="left:522px;width:153px">Tarnbeck</div>
<div class="client" style="left:707px;width:153px"><i></i>Vantor</div>
<div class="client" style="left:862px;width:218px;font-size:30px">Ostrel</div>

<!-- Contact -->
<div class="abs contact" role="img" aria-label="Faded excavator backdrop in navy tones"></div>
<svg class="abs" style="left:0;top:3500px" width="1200" height="160" viewBox="0 0 1200 160">
  <polygon points="0,0 1200,0 1200,12 0,22" fill="var(--panel)"/>
  <polygon points="700,88 1200,12 1200,140" fill="#000"/>
</svg>
<svg class="abs" style="left:560px;top:3672px" width="80" height="16" viewBox="0 0 80 16"><line x1="4" y1="8" x2="30" y2="8" stroke="#fff" stroke-width="2"/><rect x="35" y="3" width="10" height="10" fill="#fff" transform="rotate(45 40 8)"/><line x1="50" y1="8" x2="76" y2="8" stroke="#fff" stroke-width="2"/></svg>
<h2 class="abs head sec-title" style="top:3698px;color:#fff">Contact Us</h2>
<div class="field" style="left:205px;top:3775px;width:385px;height:47px">First Name</div>
<div class="field" style="left:609px;top:3775px;width:386px;height:47px">Last Name</div>
<div class="field" style="left:205px;top:3842px;width:385px;height:47px">Email</div>
<div class="field" style="left:609px;top:3842px;width:386px;height:47px">Phone</div>
<div class="field" style="left:205px;top:3910px;width:790px;height:118px">Message</div>
<div class="btn dark" style="left:510px;top:4076px;width:181px;height:44px">Submit <span class="dot" style="background:#fff"></span></div>

<!-- Footer -->
<footer class="abs footer"></footer>
<div class="abs logo" style="top:4260px;left:145px;width:122px"><div class="name" style="color:#fff;font-size:36px;line-height:36px">HBR</div><div class="sub" style="color:#fff;font-size:10px">PLANT HIRE</div></div>
<div class="flinks"><span>Home</span><span>|</span><span>About Us</span><span>|</span><span>Plant Hire</span><span>|</span><span>Policies</span><span>|</span><span>Contact Us</span></div>
<div class="social" style="left:932px"></div>
<div class="social" style="left:976px"></div>
<div class="social" style="left:1020px"></div>
<div class="finfo" style="left:145px"><div class="fic"><svg width="10" height="14" viewBox="0 0 10 14"><path d="M5 0a5 5 0 015 5c0 4-5 9-5 9S0 9 0 5a5 5 0 015-5z" fill="#fff"/><circle cx="5" cy="5" r="2" fill="var(--navy)"/></svg></div><div><b>Office Address</b><span>14 Ridgeline Rd, Yatala QLD 4207</span></div></div>
<div class="finfo" style="left:455px"><div class="fic"><svg width="12" height="12" viewBox="0 0 24 24"><path d="M6.6 10.8c1.4 2.8 3.8 5.1 6.6 6.6l2.2-2.2c.3-.3.7-.4 1-.2 1.1.4 2.3.6 3.6.6.6 0 1 .4 1 1V20c0 .6-.4 1-1 1C10.6 21 3 13.4 3 4c0-.6.4-1 1-1h3.5c.6 0 1 .4 1 1 0 1.3.2 2.5.6 3.6.1.3 0 .7-.2 1z" fill="#fff"/></svg></div><div><b>Phone</b><span>1300 462 915</span></div></div>
<div class="finfo" style="left:666px"><div class="fic"><svg width="12" height="12" viewBox="0 0 12 12"><rect x="1" y="4" width="10" height="6" fill="#fff"/><rect x="3" y="1" width="6" height="3" fill="#fff"/></svg></div><div><b>Fax</b><span>07 3402 7718</span></div></div>
<div class="finfo" style="left:867px"><div class="fic"><svg width="12" height="9" viewBox="0 0 16 12"><rect x="0.5" y="0.5" width="15" height="11" fill="#fff"/><path d="M1 1l7 6 7-6" fill="none" stroke="var(--navy)"/></svg></div><div><b>Email</b><span>info@harlowbrentmere.com</span></div></div>
<div class="copy">© 2024 Harlow Brentmere Resources . All Rights Reserved &nbsp; | &nbsp; Privacy Policy &nbsp; | &nbsp; Terms &amp; Condition</div>

</body>
</html>
```